New italian pizza restaurant in Australia, looking for a clean and crisp new take away leaflet de...

We require a leaflet for a take away menu / introduction to the area for our new italian pizza restaurant. AS we are a brand new business we need to get the word out about opening and specials as well as a takeaway menu. I have attached logo and menu items along with a basic design concept to help speed up the process.

Target Market(s)

Widest age range possible, families

Colors

Designer to choose colors to be used in the design.

```html
<!DOCTYPE html>
<html lang="en">
<head>
<meta charset="utf-8">
<title>Marlowe Pizzeria – Takeaway Menu</title>
<link rel="stylesheet" href="https://fonts.googleapis.com/css2?family=Oswald:wght@300;400;500&family=Roboto+Condensed:ital,wght@0,400;0,700;1,300;1,400&family=Didact+Gothic&display=swap">
<style>
:root{
  --page:#ffffff;
  --board:#161616;
  --board-edge:#0b0b0b;
  --chalk:#f2f2f2;
  --chalk-line:rgba(255,255,255,.6);
  --frame:rgba(255,255,255,.5);
  --red:#e8441f;
  --desc-red:#d2391b;
  --green:#2f8d4b;
  --label-green:#48a25a;
  --kids-yellow:#e7c42c;
  --kids-orange:#e9752a;
}
*{box-sizing:border-box;margin:0;padding:0}
html,body{width:767px;height:1200px;overflow:hidden;background:var(--page)}
.canvas{position:relative;width:767px;height:1200px;background:var(--page)}
.sheet{position:absolute;background:radial-gradient(ellipse at 50% 40%,#242424 0%,var(--board) 55%,var(--board-edge) 100%);overflow:hidden}
.sheet--outside{left:11px;top:16px;width:744px;height:578px}
.sheet--inside{left:11px;top:606px;width:741px;height:576px}
.frame{position:absolute;border:1px solid var(--frame)}
.abs{position:absolute}
.heading{position:absolute;font-family:"Didact Gothic",sans-serif;color:var(--chalk);letter-spacing:1.5px;text-align:center;font-size:20px;line-height:1}
.rule{position:absolute;height:1px;background:var(--chalk-line)}
.item{position:absolute;display:flex;justify-content:space-between;font-family:"Roboto Condensed",sans-serif;font-weight:700;color:var(--chalk);font-size:9px;line-height:1}
.desc{position:absolute;font-family:"Roboto Condensed",sans-serif;font-style:italic;font-weight:300;color:var(--desc-red);font-size:7.3px;line-height:1.2}
.desc--white{color:#e8e8e8}
.combo-title{color:var(--red)}
.contact{position:absolute;left:342px;font-family:"Oswald",sans-serif;font-weight:300;color:var(--chalk);font-size:17px;line-height:1}
.contact-icon{position:absolute;left:307px;width:23px;height:23px}
.brand{position:absolute;width:190px;text-align:center;font-family:"Oswald",sans-serif;font-weight:400;color:var(--chalk);font-size:22px;letter-spacing:1px;line-height:1}
.brand-dot{position:absolute;width:22px;height:22px;border-radius:50%;background:var(--red)}
.photo{position:absolute}
.order-banner{position:absolute;left:566px;top:514px;width:124px;height:28px;background:var(--red);color:#fff;font-family:"Oswald",sans-serif;font-size:17px;text-align:center;line-height:28px}
.order-web{position:absolute;left:566px;top:546px;width:124px;height:17px;background:var(--green);color:#fff;font-family:"Oswald",sans-serif;font-size:12.5px;letter-spacing:.8px;text-align:center;line-height:17px}
.pizza-row{position:absolute;left:36px;width:206px;height:20px;font-family:"Roboto Condensed",sans-serif;color:var(--chalk)}
.pizza-row .name{position:absolute;left:0;top:0;font-weight:700;font-size:9px}
.pizza-row .lbl{position:absolute;top:1px;font-size:7.5px;color:var(--label-green)}
.pizza-row .pr{position:absolute;top:0;font-weight:700;font-size:9px}
.pizza-row .l-s{left:79px}.pizza-row .p-s{left:99px}
.pizza-row .l-l{left:119px}.pizza-row .p-l{left:138px}
.pizza-row .l-f{left:163px}.pizza-row .p-f{right:0}
.pizza-row .desc{left:0;top:10px;width:210px}
.meal{position:absolute;left:278px;width:206px;height:22px}
.meal .item{left:0;right:0;top:0}
.meal .desc{left:0;top:10px;white-space:nowrap}
.subhead{position:absolute;font-family:"Roboto Condensed",sans-serif;font-style:italic;color:var(--chalk);font-size:9px;text-align:center}
.kids{position:absolute;left:557px;top:826px;font-family:"Didact Gothic",sans-serif;font-size:20px;letter-spacing:2px;line-height:1}
.kids .k1{color:var(--kids-yellow)}.kids .k2{color:var(--kids-orange)}.kids .k3{color:var(--red)}.kids .k4{color:var(--label-green)}
.price-badge{position:absolute;left:695px;top:824px;width:30px;height:30px;border-radius:50%;background:var(--red);color:#fff;font-family:"Oswald",sans-serif;font-size:10px;text-align:center;line-height:30px}
</style>
</head>
<body>
<main class="canvas">

  <!-- Outside sheet -->
  <section class="sheet sheet--outside" aria-label="Outside of leaflet"></section>

  <div class="frame" style="left:28px;top:42px;width:226px;height:527px"></div>
  <div class="frame" style="left:270px;top:257px;width:225px;height:312px"></div>

  <h2 class="heading" style="left:28px;width:226px;top:57px">SIDES</h2>
  <div class="rule" style="left:36px;width:204px;top:81px"></div>
  <div class="item" style="left:37px;width:205px;top:95px"><span>Garlic Bread</span><span>$ 4.5</span></div>
  <div class="item" style="left:37px;width:205px;top:113px"><span>Chips</span><span>$ 7.5</span></div>
  <div class="item" style="left:37px;width:205px;top:130px"><span>Garden Salad</span><span>$&nbsp;&nbsp;&nbsp;5</span></div>

  <h2 class="heading" style="left:28px;width:226px;top:164px">DESSERTS</h2>
  <div class="rule" style="left:36px;width:204px;top:187px"></div>
  <div class="item" style="left:37px;width:205px;top:201px"><span>Gelati 500mls Varieties</span><span>$ 6.5</span></div>
  <div class="item" style="left:37px;width:205px;top:219px"><span>Baci</span><span>$&nbsp;&nbsp;&nbsp;6</span></div>
  <div class="item" style="left:37px;width:205px;top:236px"><span>Tartufo</span><span>$&nbsp;&nbsp;&nbsp;6</span></div>
  <div class="item" style="left:37px;width:205px;top:254px"><span>Chocolate Mousse</span><span>$&nbsp;&nbsp;&nbsp;6</span></div>

  <h2 class="heading" style="left:28px;width:226px;top:285px">DRINKS</h2>
  <div class="rule" style="left:36px;width:204px;top:308px"></div>
  <div class="item" style="left:37px;width:205px;top:323px"><span>Soft drinks 375ml</span><span>$ 2.5</span></div>
  <div class="item" style="left:37px;width:205px;top:341px"><span>Soft drinks 1.25L</span><span>$ 4.5</span></div>
  <div class="item" style="left:37px;width:205px;top:358px"><span>Water 600ml</span><span>$ 2.5</span></div>

  <h2 class="heading combo-title" style="left:28px;width:226px;top:392px">COMBO DEALS</h2>
  <div class="rule" style="left:36px;width:204px;top:416px"></div>
  <div class="item" style="left:37px;width:205px;top:429px"><span>ANY 2 FAMILY PIZZAS,</span></div>
  <div class="item" style="left:37px;width:205px;top:447px"><span>garlic bread and 1.25l soft drink</span><span>$41.00</span></div>
  <div class="item" style="left:37px;width:205px;top:464px"><span>1 LARGE PIZZA,</span></div>
  <div class="item" style="left:37px;width:205px;top:482px"><span>1 pasta, garlic bread and 1.25l soft drink</span><span>$38.00</span></div>
  <div class="item" style="left:37px;width:205px;top:499px"><span>2 LARGE PIZZAS,</span></div>
  <div class="item" style="left:37px;width:205px;top:517px"><span>1 garlic bread and 1.25l soft drink</span><span>$36.00</span></div>

  <!-- Brand name blocks -->
  <div class="brand-dot" style="left:369px;top:108px"></div>
  <div class="brand" style="left:285px;top:140px">MARLOWE PIZZERIA</div>
  <div class="brand-dot" style="left:617px;top:108px"></div>
  <div class="brand" style="left:533px;top:140px">MARLOWE PIZZERIA</div>

  <!-- Contact -->
  <svg class="contact-icon" style="top:311px" viewBox="0 0 24 24" aria-hidden="true"><circle cx="12" cy="12" r="12" fill="#2f8d4b"/><path d="M8.6 6.5l1.8 2.6-1.1 1.3c.7 1.6 2 2.9 3.6 3.6l1.3-1.1 2.6 1.8-.9 2.2c-4.4-.2-8.3-4.1-8.5-8.5z" fill="#fff"/></svg>
  <div class="contact" style="top:312px">03 9412 7750</div>
  <svg class="contact-icon" style="top:343px" viewBox="0 0 24 24" aria-hidden="true"><circle cx="12" cy="12" r="12" fill="#2f8d4b"/><rect x="6" y="8" width="12" height="8.5" fill="none" stroke="#fff" stroke-width="1.3"/><path d="M6 8l6 5 6-5" fill="none" stroke="#fff" stroke-width="1.3"/></svg>
  <div class="contact" style="top:343px">hello@marlowepizza.com</div>
  <svg class="contact-icon" style="top:375px" viewBox="0 0 24 24" aria-hidden="true"><circle cx="12" cy="12" r="12" fill="#2f8d4b"/><circle cx="12" cy="12" r="6" fill="none" stroke="#fff" stroke-width="1.2"/><ellipse cx="12" cy="12" rx="2.6" ry="6" fill="none" stroke="#fff" stroke-width="1.1"/><path d="M6 12h12M7 9h10M7 15h10" stroke="#fff" stroke-width="1"/></svg>
  <div class="contact" style="top:376px">www.marlowepizza.com</div>
  <svg class="contact-icon" style="top:406px" viewBox="0 0 24 24" aria-hidden="true"><circle cx="12" cy="12" r="12" fill="#2f8d4b"/><path d="M12 5a4.5 4.5 0 0 0-4.5 4.5C7.5 13 12 19 12 19s4.5-6 4.5-9.5A4.5 4.5 0 0 0 12 5z" fill="#fff"/><circle cx="12" cy="9.6" r="1.7" fill="#2f8d4b"/></svg>
  <div class="contact" style="top:407px">14 Carrow St</div>
  <div class="contact" style="top:429px">Westmeadow 3049</div>

  <div class="abs" style="left:370px;top:489px;width:24px;height:24px;border-radius:50%;background:#fff"></div>
  <div class="contact" style="left:270px;width:225px;text-align:center;top:517px;font-size:15px">marlowe_pizzeria</div>
  <div class="abs" style="left:346px;top:545px;width:82px;height:3px;background:var(--green)"></div>

  <!-- Hero photo -->
  <div class="photo" role="img" aria-label="Photo of a pepperoni and rocket pizza on a wooden board, with a hand holding a phone showing an order screen" style="left:506px;top:248px;width:249px;height:346px;background:radial-gradient(circle at 45% 42%,#e0a85a 0%,#c9763a 30%,#8d3d22 48%,rgba(22,22,22,0) 62%)"></div>
  <div class="photo" role="img" aria-label="Sliced tomato" style="left:716px;top:246px;width:40px;height:58px;border-radius:50% 0 0 50%;background:radial-gradient(circle,#d8332a,#8c1a14)"></div>
  <div class="photo" role="img" aria-label="Sliced tomato" style="left:476px;top:548px;width:62px;height:46px;border-radius:50% 50% 0 0;background:radial-gradient(circle at 50% 80%,#d8332a,#8c1a14)"></div>
  <div class="order-banner">Order Online</div>
  <div class="order-web">www.marlowepizza.com</div>

  <!-- Inside sheet -->
  <section class="sheet sheet--inside" aria-label="Inside of leaflet"></section>

  <div class="frame" style="left:30px;top:625px;width:222px;height:545px"></div>
  <div class="frame" style="left:270px;top:625px;width:222px;height:545px"></div>
  <div class="frame" style="left:510px;top:625px;width:222px;height:545px"></div>

  <div class="photo" role="img" aria-label="Red capsicum and tomato slices" style="left:11px;top:606px;width:55px;height:45px;background:radial-gradient(circle at 30% 30%,#c92a1e,rgba(22,22,22,0) 75%)"></div>
  <div class="photo" role="img" aria-label="Sliced tomato" style="left:222px;top:606px;width:58px;height:34px;border-radius:0 0 50% 50%;background:radial-gradient(circle at 50% 20%,#d8332a,#8c1a14)"></div>
  <div class="photo" role="img" aria-label="Red chilli" style="left:440px;top:610px;width:60px;height:28px;background:radial-gradient(ellipse,#a51e18,rgba(22,22,22,0) 70%)"></div>
  <div class="photo" role="img" aria-label="Cucumber and feta cheese" style="left:700px;top:606px;width:52px;height:80px;background:radial-gradient(circle at 60% 65%,#efe8d5 0%,#7cae3d 35%,rgba(22,22,22,0) 70%)"></div>

  <!-- Pizza -->
  <h2 class="heading" style="left:30px;width:222px;top:640px">PIZZA</h2>
  <div class="rule" style="left:36px;width:208px;top:666px"></div>

  <div class="pizza-row" style="top:679px"><span class="name">1. Capricciosa</span><span class="lbl l-s">Small</span><span class="pr p-s">$9</span><span class="lbl l-l">Large</span><span class="pr p-l">$15</span><span class="lbl l-f">Family</span><span class="pr p-f">$18</span><span class="desc">tomato, cheese, ham, mushrooms, olives</span></div>
  <div class="pizza-row" style="top:703px"><span class="name">2. Napoli</span><span class="lbl l-s">Small</span><span class="pr p-s">$9</span><span class="lbl l-l">Large</span><span class="pr p-l">$15</span><span class="lbl l-f">Family</span><span class="pr p-f">$18</span><span class="desc">tomato, cheese, olives, anchovies</span></div>
  <div class="pizza-row" style="top:728px"><span class="name">3. American</span><span class="lbl l-s">Small</span><span class="pr p-s">$9</span><span class="lbl l-l">Large</span><span class="pr p-l">$15</span><span class="lbl l-f">Family</span><span class="pr p-f">$18</span><span class="desc">tomato, cheese, salami</span></div>
  <div class="pizza-row" style="top:752px"><span class="name">4. Vegetarian</span><span class="lbl l-s">Small</span><span class="pr p-s">$9</span><span class="lbl l-l">Large</span><span class="pr p-l">$15</span><span class="lbl l-f">Family</span><span class="pr p-f">$18</span><span class="desc">tomato, cheese, mushroom, onions, capsicum, olives</span></div>
  <div class="pizza-row" style="top:776px"><span class="name">5. Seafood</span><span class="lbl l-s">Small</span><span class="pr p-s">$9.5</span><span class="lbl l-l">Large</span><span class="pr p-l">$15.5</span><span class="lbl l-f">Family</span><span class="pr p-f">$19</span><span class="desc">tomato, cheese, prawns, clams, anchovies</span></div>
  <div class="pizza-row" style="top:801px"><span class="name">6. The Hot One</span><span class="lbl l-s">Small</span><span class="pr p-s">$9</span><span class="lbl l-l">Large</span><span class="pr p-l">$15</span><span class="lbl l-f">Family</span><span class="pr p-f">$18</span><span class="desc">tomato, cheese, ham, salami, chilli</span></div>
  <div class="pizza-row" style="top:825px"><span class="name">7. Margherita</span><span class="lbl l-s">Small</span><span class="pr p-s">$8.5</span><span class="lbl l-l">Large</span><span class="pr p-l">$14.5</span><span class="lbl l-f">Family</span><span class="pr p-f">$17</span><span class="desc">tomato, cheese, oregano</span></div>
  <div class="pizza-row" style="top:849px"><span class="name">8. The Lot</span><span class="lbl l-s">Small</span><span class="pr p-s">$10</span><span class="lbl l-l">Large</span><span class="pr p-l">$16</span><span class="lbl l-f">Family</span><span class="pr p-f">$19</span><span class="desc">tomato, cheese, ham, salami, bacon, mushroom, onions, capsicum, pineapple, olives</span></div>
  <div class="pizza-row" style="top:882px"><span class="name">9. Mexican</span><span class="lbl l-s">Small</span><span class="pr p-s">$9</span><span class="lbl l-l">Large</span><span class="pr p-l">$15</span><span class="lbl l-f">Family</span><span class="pr p-f">$18</span><span class="desc">tomato, cheese, salami, capsicum, chilli</span></div>
  <div class="pizza-row" style="top:906px"><span class="name">10. Chicken</span><span class="lbl l-s">Small</span><span class="pr p-s">$9</span><span class="lbl l-l">Large</span><span class="pr p-l">$15</span><span class="lbl l-f">Family</span><span class="pr p-f">$18</span><span class="desc">tomato, cheese, chicken, BBQ sauce</span></div>
  <div class="pizza-row" style="top:931px"><span class="name">11. Meat Lovers</span><span class="lbl l-s">Small</span><span class="pr p-s">$10</span><span class="lbl l-l">Large</span><span class="pr p-l">$16</span><span class="lbl l-f">Family</span><span class="pr p-f">$19</span><span class="desc">tomato, cheese, ham, salami, bacon, BBQ sauce</span></div>
  <div class="pizza-row" style="top:955px"><span class="name">12. The House Pizza</span><span class="lbl l-s">Small</span><span class="pr p-s">$9</span><span class="lbl l-l">Large</span><span class="pr p-l">$15</span><span class="lbl l-f">Family</span><span class="pr p-f">$18</span><span class="desc">tomato, cheese, ham, mushroom, capsicum</span></div>
  <div class="pizza-row" style="top:980px"><span class="name">13. Ceaser's Pizza</span><span class="lbl l-s">Small</span><span class="pr p-s">$10</span><span class="lbl l-l">Large</span><span class="pr p-l">$16</span><span class="lbl l-f">Family</span><span class="pr p-f">$19</span><span class="desc">tomato, cheese, ham, mushroom, pineapple, prawns</span></div>
  <div class="pizza-row" style="top:1004px"><span class="name">14. The Breakie Pizza</span><span class="lbl l-s">Small</span><span class="pr p-s">$9</span><span class="lbl l-l">Large</span><span class="pr p-l">$15</span><span class="lbl l-f">Family</span><span class="pr p-f">$18</span><span class="desc">tomato, cheese, bacon, egg</span></div>
  <div class="pizza-row" style="top:1028px"><span class="name">15. The Footy</span><span class="lbl l-s">Small</span><span class="pr p-s">$9</span><span class="lbl l-l">Large</span><span class="pr p-l">$15</span><span class="lbl l-f">Family</span><span class="pr p-f">$18</span><span class="desc">Special tomato, cheese, ham, capsicum, onions, pineapple</span></div>
  <div class="pizza-row" style="top:1053px"><span class="name">16. The Marlowe</span><span class="lbl l-s">Small</span><span class="pr p-s">$9</span><span class="lbl l-l">Large</span><span class="pr p-l">$15</span><span class="lbl l-f">Family</span><span class="pr p-f">$18</span><span class="desc">tomato, cheese ham, mushrooms, onions, olives</span></div>
  <div class="pizza-row" style="top:1077px"><span class="name">17. The Carrow Special</span><span class="lbl l-s">Small</span><span class="pr p-s">$10</span><span class="lbl l-l">Large</span><span class="pr p-l">$16</span><span class="lbl l-f">Family</span><span class="pr p-f">$19</span><span class="desc">tomato, cheese, ham, onions, bacon, egg</span></div>
  <div class="pizza-row" style="top:1102px"><span class="name">18. Ham</span><span class="lbl l-s">Small</span><span class="pr p-s">$8.5</span><span class="lbl l-l">Large</span><span class="pr p-l">$14.5</span><span class="lbl l-f">Family</span><span class="pr p-f">$17</span><span class="desc">tomato, cheese, ham</span></div>
  <div class="pizza-row" style="top:1126px"><span class="name">19. Garlic</span><span class="lbl l-s">Small</span><span class="pr p-s">$8.5</span><span class="lbl l-l">Large</span><span class="pr p-l">$14.5</span><span class="lbl l-f">Family</span><span class="pr p-f">$17</span><span class="desc">garlic, cheese, oregano</span></div>

  <div class="photo" role="img" aria-label="Sliced salami" style="left:36px;top:1148px;width:70px;height:34px;border-radius:50% 50% 0 0;background:radial-gradient(circle at 50% 90%,#c0343a,#7a1c20)"></div>

  <!-- Main meals -->
  <h2 class="heading" style="left:270px;width:222px;top:641px;font-size:21px">MAIN MEALS</h2>
  <div class="rule" style="left:278px;width:30px;top:667px"></div>
  <div class="rule" style="left:454px;width:30px;top:667px"></div>
  <div class="subhead" style="left:270px;width:222px;top:661px">all mains served with chips or salad</div>

  <div class="meal" style="top:679px"><div class="item"><span>Scotch Fillet Steak 300g</span><span>$&nbsp;&nbsp;25</span></div><span class="desc">grass fed, with your choice of Mushroom, Pepper or Garlic sauce</span></div>
  <div class="meal" style="top:705px"><div class="item"><span>Calamari</span><span>$ 19.5</span></div><span class="desc">Flash fried or crumbed squid with aioli</span></div>
  <div class="meal" style="top:731px"><div class="item"><span>Chicken Parmigiana</span><span>$ 19.5</span></div><span class="desc">Schnitzel topped with ham, Napoli sauce &amp; mozzarella</span></div>
  <div class="meal" style="top:757px"><div class="item"><span>Veal Scallopini</span><span>$ 19.5</span></div><span class="desc">with your choice of mushroom or creamy avocado sauce</span></div>
  <div class="meal" style="top:783px"><div class="item"><span>Veal Parmigiana</span><span>$ 19.5</span></div><span class="desc">schnitzel topped ham, Napoli sauce &amp; mozzarella</span></div>

  <h2 class="heading" style="left:270px;width:222px;top:831px;font-size:19px;letter-spacing:.5px">PASTA- SPAGHETTI,</h2>
  <div class="heading" style="left:270px;width:222px;top:851px;font-size:9px;letter-spacing:.5px">PENNE, GNOCCHI, FETTUCINE, LINGUINE</div>
  <div class="rule" style="left:278px;width:206px;top:882px"></div>

  <div class="meal" style="top:890px"><div class="item"><span>Bolognese</span><span>$&nbsp;&nbsp;14</span></div><span class="desc">traditional Italian meat sauce</span></div>
  <div class="meal" style="top:916px"><div class="item"><span>Carbonara</span><span>$&nbsp;&nbsp;14</span></div><span class="desc">onion, bacon, egg in creamy parmesan cheese sauce</span></div>
  <div class="meal" style="top:942px"><div class="item"><span>Napolitana</span><span>$ 13.5</span></div><span class="desc">traditional Italian Napoli sauce</span></div>
  <div class="meal" style="top:968px"><div class="item"><span>Amatriciana</span><span>$&nbsp;&nbsp;15</span></div><span class="desc">bacon, onion, olives, capsicum, fresh chili cooked in Napoli sauce</span></div>
  <div class="meal" style="top:994px"><div class="item"><span>Marinara</span><span>$&nbsp;&nbsp;15</span></div><span class="desc">mussels, prawns, calamari, scallops cooked in Napoli sauce</span></div>
  <div class="meal" style="top:1020px"><div class="item"><span>Risotto Polo</span><span>$ 16.5</span></div><span class="desc">chicken, mushroom, onion, cooked in a cream sauce</span></div>
  <div class="meal" style="top:1046px"><div class="item"><span>Lasagna</span><span>$&nbsp;&nbsp;15</span></div><span class="desc">Homemade Lasagna</span></div>
  <div class="meal" style="top:1072px"><div class="item"><span>Pasta Your way</span><span>$ 14.5</span></div><span class="desc">choose any three ingredients with cream or Napoli sauce</span></div>

  <div class="photo" role="img" aria-label="Row of dried pasta shapes: penne, farfalle, fettuccine, spaghetti nest, fusilli" style="left:262px;top:1130px;width:236px;height:48px;background:linear-gradient(90deg,rgba(22,22,22,0),#d9b56a 12%,#e3c27e 50%,#d9b56a 88%,rgba(22,22,22,0));border-radius:20px"></div>

  <!-- Salads -->
  <h2 class="heading" style="left:510px;width:222px;top:641px">SALADS</h2>
  <div class="rule" style="left:524px;width:196px;top:667px"></div>

  <div class="item" style="left:517px;width:205px;top:691px"><span>Greek Salad</span><span>$ 14.5</span></div>
  <div class="desc desc--white" style="left:517px;top:701px">cos lettuce, tomato, onion, cucumber, olives, feta cheese &amp; dressing</div>
  <div class="item" style="left:517px;width:205px;top:717px"><span>Grilled Chicken Salad</span><span>$ 15.5</span></div>
  <div class="desc desc--white" style="left:517px;top:727px;width:205px">Seasoned chicken, mixed leaves, cherry tomato, Spanish onion, cucumber with garlic infused olive oil</div>
  <div class="item" style="left:517px;width:205px;top:752px"><span>Chicken Ceasar Salad</span><span>$ 15.5</span></div>
  <div class="desc desc--white" style="left:517px;top:762px;width:205px">Chicken, cos lettuce, croutons, shaved parmesan, anchovies, egg, bacon served with ceaser dressing</div>

  <div class="kids"><span class="k1">KI</span><span class="k2">DS</span> <span class="k3">ME</span><span class="k4">NU</span></div>
  <div class="price-badge">$ 9.5</div>
  <div class="rule" style="left:524px;width:196px;top:851px"></div>

  <div class="item" style="left:516px;width:203px;top:863px"><span>Pasta Bolognese</span><span>$ 9.5</span></div>
  <div class="item" style="left:516px;width:203px;top:881px"><span>Pasta Napoli</span><span>$ 9.5</span></div>
  <div class="item" style="left:516px;width:203px;top:898px"><span>Chicken Nuggets &amp; Chips</span><span>$ 9.5</span></div>
  <div class="item" style="left:516px;width:203px;top:915px"><span>Cheeseburger &amp; Chips</span><span>$ 9.5</span></div>

  <div class="photo" role="img" aria-label="Salami slices, parmesan wedge, capsicum and herbs" style="left:530px;top:940px;width:222px;height:90px;background:radial-gradient(ellipse at 55% 50%,#b63338 0%,#6e1e22 35%,rgba(22,22,22,0) 70%)"></div>
  <div class="photo" role="img" aria-label="Pepperoni and rocket pizza with chilli" style="left:560px;top:1010px;width:192px;height:172px;background:radial-gradient(circle at 70% 85%,#e0a85a 0%,#c9763a 35%,#8d3d22 55%,rgba(22,22,22,0) 72%)"></div>

</main>
</body>
</html>
```